business card

Business card for new business.
Red and black corporate colors.
Card can have an Indsutrial feel to it. Feel free to add Rust, Bolted steel, or graphics as you see fit. We provide highly specialized services to the below mentioned industries.
Keep information out of corners so that if I want I can choose rounded corners.
Information
- front. name - title - phone - email
- Rear
Refining - Rail - Infrastructure - Mining - Energy
Calgary - Edmonton - Fort McMurray - Revelstoke - Vancouver

```html
<!DOCTYPE html>
<html lang="en">
<head>
<meta charset="UTF-8">
<title>Girderline Business Card</title>
<link href="https://fonts.googleapis.com/css2?family=Arimo:wght@400;700&display=swap" rel="stylesheet">
<style>
  :root {
    --backdrop: #1d1d20;
    --card-black: #030303;
    --brand-red: #ee1f26;
    --text-grey: #9a9a9a;
    --logo-grey: #b4b4b4;
  }
  html, body {
    margin: 0;
    padding: 0;
    width: 1200px;
    height: 800px;
    overflow: hidden;
    background: var(--backdrop);
    font-family: "Arimo", Arial, sans-serif;
  }
  .stage {
    position: relative;
    width: 1200px;
    height: 800px;
  }
  .card {
    position: absolute;
    top: 245px;
    width: 540px;
    height: 310px;
    background: var(--card-black);
    box-shadow: 0 14px 30px rgba(0,0,0,0.55);
    overflow: hidden;
  }
  .card--back { left: 40px; }
  .card--front { left: 620px; }

  .band {
    position: absolute;
    top: 262px;
    height: 22px;
    background: var(--brand-red);
  }

  /* back side */
  .card--back .band--lead { left: 0; width: 88px; }
  .card--back .band--trail { left: 222px; right: 0; }
  .brand {
    position: absolute;
    left: 98px;
    top: 259px;
    height: 28px;
    display: flex;
    align-items: center;
    gap: 7px;
  }
  .brand__mark {
    width: 9px;
    height: 9px;
    background: var(--brand-red);
  }
  .brand__name {
    color: var(--logo-grey);
    font-weight: 700;
    font-size: 14px;
    letter-spacing: 0.5px;
  }
  .services {
    position: absolute;
    left: 40px;
    right: 40px;
    top: 100px;
    text-align: center;
    line-height: 1;
  }
  .services__industries {
    color: var(--logo-grey);
    font-size: 14px;
    font-weight: 700;
    letter-spacing: 1px;
  }
  .services__rule {
    width: 60px;
    height: 2px;
    background: var(--brand-red);
    margin: 14px auto;
  }
  .services__cities {
    color: var(--text-grey);
    font-size: 11.5px;
    letter-spacing: 0.5px;
  }
  .sep { color: var(--brand-red); padding: 0 5px; }

  /* front side */
  .card--front .band--lead { left: 0; width: 178px; }
  .card--front .band--end { right: 0; width: 56px; }
  .contact-row {
    position: absolute;
    left: 190px;
    top: 253px;
    height: 40px;
    display: flex;
    align-items: center;
    gap: 11px;
  }
  .identity { line-height: 1; }
  .identity__name {
    color: var(--brand-red);
    font-size: 16px;
    font-weight: 400;
    letter-spacing: 0.2px;
  }
  .identity__title {
    color: var(--text-grey);
    font-size: 11.5px;
    margin-top: 3px;
  }
  .divider {
    width: 1px;
    height: 34px;
    background: var(--brand-red);
  }
  .details {
    display: flex;
    flex-direction: column;
    gap: 5px;
    color: var(--text-grey);
    font-size: 10.5px;
  }
  .details__line {
    display: flex;
    align-items: center;
    gap: 5px;
  }
  .details__icon { width: 9px; height: 9px; display: block; }
</style>
</head>
<body>
<main class="stage">

  <section class="card card--back" aria-label="Card back">
    <div class="services">
      <div class="services__industries">REFINING<span class="sep">|</span>RAIL<span class="sep">|</span>INFRASTRUCTURE<span class="sep">|</span>MINING<span class="sep">|</span>ENERGY</div>
      <div class="services__rule"></div>
      <div class="services__cities">Calgary<span class="sep">•</span>Edmonton<span class="sep">•</span>Fort McMurray<span class="sep">•</span>Revelstoke<span class="sep">•</span>Vancouver</div>
    </div>
    <div class="band band--lead"></div>
    <div class="brand">
      <span class="brand__mark"></span>
      <span class="brand__name">GIRDERLINE</span>
    </div>
    <div class="band band--trail"></div>
  </section>

  <section class="card card--front" aria-label="Card front">
    <div class="band band--lead"></div>
    <div class="contact-row">
      <div class="identity">
        <div class="identity__name">DANA WHITLOCK</div>
        <div class="identity__title">Managing Director</div>
      </div>
      <div class="divider"></div>
      <div class="details">
        <div class="details__line">
          <svg class="details__icon" viewBox="0 0 10 10" aria-hidden="true">
            <path d="M1 3 Q5 0 9 3 L8 4.5 L6.5 3.8 L6.5 3 Q5 2.5 3.5 3 L3.5 3.8 L2 4.5 Z M2.5 5 H7.5 L8.5 9 H1.5 Z" fill="#ee1f26"/>
          </svg>
          <span>(01) 5550 1427</span>
        </div>
        <div class="details__line">
          <svg class="details__icon" viewBox="0 0 10 10" aria-hidden="true">
            <rect x="0.5" y="2" width="9" height="6.5" fill="#ee1f26"/>
            <path d="M0.8 2.3 L5 5.8 L9.2 2.3" stroke="#030303" stroke-width="0.9" fill="none"/>
          </svg>
          <span>info@girderline.com</span>
        </div>
      </div>
    </div>
    <div class="band band--end"></div>
  </section>

</main>
</body>
</html>
```